San Francisco Leading Consulting firm - 47Vora Web Design Project

•Create a Web Design
•Uncoded webpage layout design
•2 Pages Design - Homepage + Interior Page

Task Description
Hello, we're looking for a re-design our current website www.47vora-example.com

we have a sample mockup design @

http://47vora.pubtrellis-example.org/

This shows the layout that we like and also a sample of 6 pictures that would change based on where you mouse over..

6 pictures HOME design needs to be included.

SMART
THOUGHTFUL
FLEXIBLE
CREATIVE SERVICES
TECHNICAL SERVICES
PARTNERS

sites we like:

http://www.melvanadvisory-example.com/Home.cfm?id=Home
http://www.plinthworks-example.com/index.html

Our company can be best described as: 100+ employees, cutting-edge, depandable, innovative, strong, smart.

Our Primary focus is: IT Consulting Services and Creative Design services

47Vora LLC is a consulting firm providing creative design, business and technology solutions to both private and public interests.

Established in 1996, 47Vora is a San Francisco based company providing specialists for a range of business needs including:

Creative Design Services
•Print
•Logo Design
•Website Design
•Illustration

and

Business and Technology solutions

•Application Software and Web Development
•Business Process Re-Design (BPR)
•Business/Systems Analysis and Requirement Documentation
•Mentoring and Training
•Network/Hardware Installation Services
•System Design and Architecture
•Vendor Management
•Docuvault Architecture and Implementation

our sample mockup site:

Reason: Due to holiday season, we're not available to work with designers and finilize our design.  

Thank you very much for submitting your design.

We appreciate your time and creativity.   Since, our office is currently closed for holidays, we will be reviewing it in details next week and will make our decision as soon as possible.

It would be great if you could submit any of your changes by Wed next week, so it would be part of our reviews. 

Please see updated wireframe under attachments:  we have some minor updates to our wireframe that we would like you to update your designs, if possible.  

We also encorouge you not to use our standard wireframe and come up with more unique designs.   Everything would be considered when we review your design.

 

Target Market(s)

Creative services and professional services clients, including government agencies

Industry/Entity Type

Business

Requirements
Must have
• Clean, professional look, easy navigation

```html
<!DOCTYPE html>
<html lang="en">
<head>
<meta charset="utf-8">
<title>47Vora — Home</title>
<link rel="stylesheet" href="https://fonts.googleapis.com/css2?family=Mulish:wght@400;600&family=Noto+Sans:wght@400&family=Archivo+Black&family=Arimo:wght@700&display=swap">
<style>
  :root {
    --blue: #1a8fc6;
    --blue-light: #6bbde2;
    --ink: #222222;
    --nav-dark: #2a2a2a;
    --nav-line: #111111;
    --strip: #4a4a4a;
    --footer: #262626;
    --rule: #b9b9b9;
    --white: #ffffff;
  }
  * { box-sizing: border-box; margin: 0; padding: 0; }
  html, body { width: 1200px; height: 900px; overflow: hidden; background: var(--white); }
  body { position: relative; font-family: "Noto Sans", sans-serif; color: var(--ink); }

  .brand { position: absolute; left: 133px; top: 22px; display: flex; align-items: center; gap: 10px; }
  .brand-mark { width: 26px; height: 26px; border-radius: 50%; background: var(--blue); }
  .brand-name { font-family: "Mulish", sans-serif; font-weight: 400; font-size: 30px; color: #555c60; letter-spacing: 1px; }

  .login { position: absolute; left: 984px; top: 0; width: 93px; height: 41px; background: linear-gradient(#3a3a3a, #151515); border-top: 7px solid var(--blue); border-radius: 0 0 4px 4px; color: var(--white); font-family: "Mulish", sans-serif; font-size: 14px; font-weight: 600; text-align: center; line-height: 34px; }

  .main-nav { position: absolute; left: 0; top: 94px; width: 1200px; height: 38px; background: linear-gradient(#363636, #1c1c1c); border-top: 1px solid var(--nav-line); }
  .nav-underline { position: absolute; left: 118px; top: 131px; width: 960px; height: 6px; background: var(--blue); border-radius: 0 0 3px 3px; }
  .nav-underline::after { content: ""; position: absolute; left: 960px; top: 0; width: 122px; height: 2px; background: var(--blue); }
  .nav-list { position: absolute; left: 119px; top: 89px; display: flex; list-style: none; height: 43px; }
  .nav-item { height: 43px; display: flex; align-items: flex-end; }
  .nav-link { display: flex; align-items: center; justify-content: center; gap: 10px; height: 38px; color: var(--white); font-family: "Mulish", sans-serif; font-size: 14px; font-weight: 600; border-right: 1px solid #0e0e0e; box-shadow: inset -1px 0 0 #444; }
  .nav-item.is-active .nav-link { height: 43px; background: linear-gradient(#2aa6dc, var(--blue)); border-radius: 4px 4px 0 0; border-right: none; box-shadow: none; }
  .nav-link svg { width: 8px; height: 11px; }

  .hero { position: absolute; left: 118px; top: 148px; width: 960px; height: 379px; background: #05070b; overflow: hidden; }
  .hero-visual { position: absolute; left: 0; top: 0; width: 600px; height: 379px; background: radial-gradient(ellipse at 35% 50%, #2f6fc4 0%, #15306a 38%, #0a1430 65%, #05070b 100%); }
  .hero-title { position: absolute; left: 391px; top: 96px; font-family: "Archivo Black", sans-serif; font-size: 46px; line-height: 1; color: var(--white); letter-spacing: -1px; }
  .hero-tagline { position: absolute; left: 393px; top: 142px; font-family: "Arimo", sans-serif; font-weight: 700; font-size: 23.5px; color: var(--blue-light); letter-spacing: -0.2px; }
  .hero-arrow { position: absolute; top: 164px; width: 30px; height: 30px; }
  .hero-arrow.prev { left: 13px; }
  .hero-arrow.next { left: 913px; }

  .thumb-strip { position: absolute; left: 118px; top: 527px; width: 960px; height: 83px; background: var(--strip); border-radius: 0 0 4px 4px; }
  .thumb { position: absolute; top: 15px; width: 160px; height: 58px; }
  .thumb.is-current { outline: 2px solid #f4f0d0; box-shadow: 0 0 8px 3px #fff6b0; }
  .thumb-1 { left: 45px; background: linear-gradient(90deg, #1b3f88, #0b1226); }
  .thumb-2 { left: 220px; background: linear-gradient(90deg, #e8e8e8, #ffffff); }
  .thumb-3 { left: 399px; background: linear-gradient(90deg, #5a5e63, #9ea3a8); }
  .thumb-4 { left: 577px; background: linear-gradient(90deg, #6f7679, #a9b0b2); }
  .thumb-5 { left: 754px; background: linear-gradient(90deg, #0a0d14, #5c7c9c 60%, #0a0d14); }

  .features { position: absolute; left: 118px; top: 648px; width: 960px; height: 172px; }
  .feature { position: absolute; top: 0; height: 172px; }
  .feature + .feature { border-left: 1px solid var(--rule); }
  .feature-1 { left: 0; width: 311px; }
  .feature-2 { left: 311px; width: 334px; }
  .feature-3 { left: 645px; width: 315px; }
  .feature-head { display: flex; align-items: center; gap: 14px; margin: 4px 0 0 8px; height: 24px; }
  .feature-2 .feature-head, .feature-2 .feature-text, .feature-2 .btn { margin-left: 19px; }
  .feature-3 .feature-head, .feature-3 .feature-text, .feature-3 .btn { margin-left: 17px; }
  .feature-head svg { width: 24px; height: 22px; flex: none; }
  .feature-title { font-family: "Mulish", sans-serif; font-weight: 400; font-size: 18px; color: var(--ink); }
  .feature-text { margin: 12px 0 0 7px; font-size: 13px; line-height: 24px; letter-spacing: 0.3px; max-width: 300px; }
  .btn { display: inline-block; margin: 14px 0 0 5px; width: 109px; height: 24px; background: linear-gradient(#27a3da, var(--blue)); border-radius: 2px; color: var(--white); font-family: "Mulish", sans-serif; font-size: 14px; font-weight: 600; text-align: center; line-height: 24px; }

  .site-footer { position: absolute; left: 0; top: 852px; width: 1200px; height: 48px; background: var(--footer); color: var(--white); font-family: "Mulish", sans-serif; font-size: 12px; font-weight: 600; text-align: center; padding-top: 7px; }
</style>
</head>
<body>
  <header>
    <div class="brand"><span class="brand-mark"></span><span class="brand-name">47Vora</span></div>
    <div class="login">LOGIN</div>
  </header>

  <nav>
    <div class="main-nav"></div>
    <div class="nav-underline"></div>
    <ul class="nav-list">
      <li class="nav-item is-active"><span class="nav-link" style="width:111px">HOME</span></li>
      <li class="nav-item"><span class="nav-link" style="width:143px">COMPANY <svg viewBox="0 0 8 11"><path d="M1 1l5 4.5L1 10" fill="none" stroke="#fff" stroke-width="2"/></svg></span></li>
      <li class="nav-item"><span class="nav-link" style="width:200px">TECHNICAL SERVICES <svg viewBox="0 0 8 11"><path d="M1 1l5 4.5L1 10" fill="none" stroke="#fff" stroke-width="2"/></svg></span></li>
      <li class="nav-item"><span class="nav-link" style="width:194px">CREATIVE SERVICES <svg viewBox="0 0 8 11"><path d="M1 1l5 4.5L1 10" fill="none" stroke="#fff" stroke-width="2"/></svg></span></li>
      <li class="nav-item"><span class="nav-link" style="width:135px">PARTNERS <svg viewBox="0 0 8 11"><path d="M1 1l5 4.5L1 10" fill="none" stroke="#fff" stroke-width="2"/></svg></span></li>
      <li class="nav-item"><span class="nav-link" style="width:139px">CONTACT US</span></li>
    </ul>
  </nav>

  <section class="hero">
    <div class="hero-visual" role="img" aria-label="Glowing blue network of neurons with orange sparks"></div>
    <h1 class="hero-title">SMART</h1>
    <p class="hero-tagline">We don’t believe in the term ‘overqualified’</p>
    <svg class="hero-arrow prev" viewBox="0 0 30 30"><circle cx="15" cy="15" r="14" fill="#e6e6e6"/><path d="M22 15H10M15 9l-6 6 6 6" fill="none" stroke="#222" stroke-width="3"/></svg>
    <svg class="hero-arrow next" viewBox="0 0 30 30"><circle cx="15" cy="15" r="14" fill="#e6e6e6"/><path d="M8 15h12M15 9l6 6-6 6" fill="none" stroke="#222" stroke-width="3"/></svg>
  </section>

  <div class="thumb-strip">
    <div class="thumb thumb-1 is-current" role="img" aria-label="Neuron network thumbnail"></div>
    <div class="thumb thumb-2" role="img" aria-label="Businessman bending backwards over a laptop"></div>
    <div class="thumb thumb-3" role="img" aria-label="Photographer crouching in a busy street"></div>
    <div class="thumb thumb-4" role="img" aria-label="Chalkboard covered in equations"></div>
    <div class="thumb thumb-5" role="img" aria-label="Flowing blue light waves on black"></div>
  </div>

  <main class="features">
    <article class="feature feature-1">
      <div class="feature-head">
        <svg viewBox="0 0 24 22"><rect x="3" y="3" width="18" height="12" fill="none" stroke="#222" stroke-width="2"/><path d="M0 18h24v2H0z" fill="#222"/></svg>
        <h2 class="feature-title">For Graphic Designers</h2>
      </div>
      <p class="feature-text">47Vora is looking for top creative talent to deliver graphic design solutions for some leading global brands Do you have what it takes?</p>
      <a class="btn">Learn More</a>
    </article>
    <article class="feature feature-2">
      <div class="feature-head">
        <svg viewBox="0 0 24 22"><path d="M12 2v18M3 11h18" stroke="#222" stroke-width="1.5"/><circle cx="12" cy="11" r="3" fill="#222"/><circle cx="12" cy="3" r="2.5" fill="#222"/><circle cx="12" cy="19" r="2.5" fill="#222"/><circle cx="3" cy="11" r="2.5" fill="#222"/><circle cx="21" cy="11" r="2.5" fill="#222"/></svg>
        <h2 class="feature-title">The 47Vora Difference</h2>
      </div>
      <p class="feature-text">Smart, Flexible, Thoughtful: find out why leading corporations and government agencies are turning to 47vora to help manage their most demanding IT services challenges.</p>
      <a class="btn">Learn More</a>
    </article>
    <article class="feature feature-3">
      <div class="feature-head">
        <svg viewBox="0 0 24 22"><circle cx="12" cy="6" r="5.5" fill="#222"/><path d="M1 22c0-7 5-10 11-10s11 3 11 10z" fill="#222"/></svg>
        <h2 class="feature-title">Team Up With the Best</h2>
      </div>
      <p class="feature-text">When it comes to technology partnerships, our mission it so make you a success.</p>
      <a class="btn">Learn More</a>
    </article>
  </main>

  <footer class="site-footer">Copyright 2010, 47Vora, LLC All rights reserved.</footer>
</body>
</html>
```